San Francisco Leading Consulting firm - 47Vora Web Design Project

•Create a Web Design
•Uncoded webpage layout design
•2 Pages Design - Homepage + Interior Page

Task Description
Hello, we're looking for a re-design our current website www.47vora-example.com

we have a sample mockup design @

http://47vora.pubtrellis-example.org/

This shows the layout that we like and also a sample of 6 pictures that would change based on where you mouse over..

6 pictures HOME design needs to be included.

SMART
THOUGHTFUL
FLEXIBLE
CREATIVE SERVICES
TECHNICAL SERVICES
PARTNERS

sites we like:

http://www.melvanadvisory-example.com/Home.cfm?id=Home
http://www.plinthworks-example.com/index.html

Our company can be best described as: 100+ employees, cutting-edge, depandable, innovative, strong, smart.

Our Primary focus is: IT Consulting Services and Creative Design services

47Vora LLC is a consulting firm providing creative design, business and technology solutions to both private and public interests.

Established in 1996, 47Vora is a San Francisco based company providing specialists for a range of business needs including:

Creative Design Services
•Print
•Logo Design
•Website Design
•Illustration

and

Business and Technology solutions

•Application Software and Web Development
•Business Process Re-Design (BPR)
•Business/Systems Analysis and Requirement Documentation
•Mentoring and Training
•Network/Hardware Installation Services
•System Design and Architecture
•Vendor Management
•Docuvault Architecture and Implementation

our sample mockup site:

Reason: Due to holiday season, we're not available to work with designers and finilize our design.  

Thank you very much for submitting your design.

We appreciate your time and creativity.   Since, our office is currently closed for holidays, we will be reviewing it in details next week and will make our decision as soon as possible.

It would be great if you could submit any of your changes by Wed next week, so it would be part of our reviews. 

Please see updated wireframe under attachments:  we have some minor updates to our wireframe that we would like you to update your designs, if possible.  

We also encorouge you not to use our standard wireframe and come up with more unique designs.   Everything would be considered when we review your design.

 

Target Market(s)

Creative services and professional services clients, including government agencies

Industry/Entity Type

Business

Requirements
Must have
• Clean, professional look, easy navigation

```html
<!DOCTYPE html>
<html lang="en">
<head>
<meta charset="utf-8">
<title>47Vora — Technology Solutions</title>
<link rel="stylesheet" href="https://fonts.googleapis.com/css2?family=Questrial&family=Arimo:wght@400;700&display=swap">
<style>
:root{
  --page-bg:#ffffff;
  --header-bg:#edf1f5;
  --band-bg:#e9eef2;
  --ink:#3c3c3c;
  --ink-soft:#555a5e;
  --muted:#8a8f94;
  --rule:#d6d9dc;
  --cyan:#3fc6e6;
  --magenta:#b5178c;
  --orange:#f0a23a;
  --sky:#27b6dd;
  --button:#7a7a7a;
  --logo-blue:#1d5fa8;
}
*{box-sizing:border-box;margin:0;padding:0}
html,body{width:1057px;height:1200px;overflow:hidden;background:var(--page-bg)}
body{position:relative;font-family:"Arimo",Arial,sans-serif;color:var(--ink)}
.abs{position:absolute}

/* header */
.site-header{left:0;top:0;width:1057px;height:100px;background:var(--header-bg)}
.brand{left:113px;top:27px;display:flex;align-items:center;gap:10px;font-family:"Questrial",sans-serif;font-size:30px;color:var(--logo-blue);letter-spacing:1px}
.brand-mark{width:22px;height:22px;border-radius:50%;background:var(--logo-blue)}
.tagline{left:295px;top:49px;font-size:12px;color:var(--ink-soft)}
.search{left:815px;top:56px;width:142px;height:21px;background:#fff;border:1px solid #e0e3e6;font-size:8px;font-style:italic;color:#9aa0a5;padding:6px 7px}
.search svg{position:absolute;right:5px;top:3px}

/* intro band */
.intro{left:0;top:100px;width:1057px;height:189px;background:#fff;box-shadow:0 2px 6px rgba(0,0,0,.06)}
.main-nav{left:113px;top:108px;width:157px;list-style:none}
.main-nav li{height:34px;border-bottom:1px dotted var(--rule);font-family:"Questrial",sans-serif;font-size:10.5px;font-weight:bold;letter-spacing:1px;color:#333;padding-top:13px;padding-left:10px}
.main-nav li:last-child{border-bottom:none}
.main-nav .chev{color:var(--orange);margin-left:5px}
.nav-divider{left:286px;top:106px;width:1px;height:166px;background:var(--rule)}
.welcome-title{left:309px;top:118px;font-family:"Questrial",sans-serif;font-size:30px;color:var(--cyan)}
.welcome-copy{left:309px;top:166px;width:640px;font-size:11.5px;line-height:21px;color:var(--ink-soft)}
.welcome-copy p{margin-bottom:11px}

/* slider */
.slider-band{left:0;top:289px;width:1057px;height:300px;background:var(--band-bg)}
.thumbs{left:157px;top:294px;width:82px}
.thumb{width:82px;height:45px;margin-bottom:4px;border:2px solid #fff}
.thumb-pointer{left:257px;top:553px}
.hero{left:265px;top:289px;width:688px;height:300px;background:linear-gradient(100deg,#c7a98c 0%,#d9c9b6 35%,#b9a284 60%,#8c7b66 100%)}
.hero-tint{left:265px;top:289px;width:161px;height:300px;background:linear-gradient(180deg,#b98a74 0%,#93927a 60%,#7e8466 100%);opacity:.9}
.hero-title{left:287px;top:484px;font-family:"Questrial",sans-serif;font-size:46px;color:#fff;line-height:1}
.hero-title .chev{color:var(--cyan);font-size:40px;margin-right:6px}
.hero-sub{left:315px;top:534px;font-family:"Questrial",sans-serif;font-size:21px;color:#fff}

/* audience columns */
.audience{top:630px;width:276px;height:287px;border-left:1px dotted #c6c9cc}
.audience .eyebrow{position:absolute;left:13px;top:4px;font-family:"Questrial",sans-serif;font-size:14px;color:var(--muted)}
.audience .eyebrow-tick{position:absolute;left:-1px;top:0;width:7px;height:14px}
.audience h2{position:absolute;left:20px;top:42px;font-family:"Questrial",sans-serif;font-size:17.5px;font-weight:bold;letter-spacing:1px}
.audience .visual{position:absolute;left:20px;top:78px;width:256px;height:80px}
.audience p{position:absolute;left:20px;top:170px;width:240px;font-size:11px;line-height:20px;color:var(--ink-soft)}
.learn-more{position:absolute;left:20px;top:250px;width:75px;height:28px;background:var(--button);color:#fff;font-size:12px;text-align:center;line-height:28px;border-radius:3px;box-shadow:1px 2px 3px rgba(0,0,0,.25)}
.col-designers{left:107px}
.col-clients{left:383px}
.col-partners{left:673px}

/* services footer */
.services{left:67px;top:957px;width:885px;height:196px;background:#fff;box-shadow:0 -6px 10px -6px rgba(0,0,0,.12),0 6px 10px -6px rgba(0,0,0,.12)}
.services h3{position:absolute;font-size:13px;font-weight:bold;color:#444}
.services ul{position:absolute;list-style:none;font-size:10px;color:#333}
.services li{margin-bottom:14px;padding-left:9px;position:relative;line-height:12px}
.services li::before{content:"•";position:absolute;left:0}
.services-divider{left:369px;top:981px;width:1px;height:157px;background:var(--rule)}
.copyright{left:0;top:1170px;width:1057px;text-align:center;font-size:10.5px;color:#222}
</style>
</head>
<body>

<header class="site-header abs"></header>
<div class="brand abs"><span class="brand-mark"></span>47Vora</div>
<div class="tagline abs">Thechnology Solutions for the 21st Century</div>
<div class="search abs">SEARCH
  <svg width="13" height="13" viewBox="0 0 13 13"><circle cx="7.5" cy="5.5" r="4" fill="none" stroke="#f0a23a" stroke-width="1.6"/><line x1="4.6" y1="8.4" x2="1.5" y2="11.5" stroke="#f0a23a" stroke-width="2"/></svg>
</div>

<section class="intro abs"></section>
<ul class="main-nav abs">
  <li>COMPANY<span class="chev">›</span></li>
  <li>TECHNICAL SERVICES<span class="chev">›</span></li>
  <li>CREATIVE SERVICES<span class="chev">›</span></li>
  <li>PARTNERS<span class="chev">›</span></li>
  <li>CONTACT US</li>
</ul>
<div class="nav-divider abs"></div>
<h1 class="welcome-title abs">welcome</h1>
<div class="welcome-copy abs">
  <p>47Vora LLC is a consulting firm providing creative design, business and technology solutions to both private and public interests.</p>
  <p>Our experts possess broad industry knowledge which can help with technical and businessprocess challenges, delivering solutions that are creative and cost effective.</p>
</div>

<section class="slider-band abs"></section>
<div class="thumbs abs">
  <div class="thumb" role="img" aria-label="Thumbnail photo: smart" style="background:linear-gradient(135deg,#9fb7c9,#d9c8b8)"></div>
  <div class="thumb" role="img" aria-label="Thumbnail photo: thoughtful" style="background:linear-gradient(135deg,#b8c2cb,#8e9aa6)"></div>
  <div class="thumb" role="img" aria-label="Thumbnail photo: flexible" style="background:linear-gradient(135deg,#c9cbc4,#8f9a88)"></div>
  <div class="thumb" role="img" aria-label="Thumbnail photo: creative services" style="background:linear-gradient(135deg,#6f7d86,#b9a85a)"></div>
  <div class="thumb" role="img" aria-label="Thumbnail photo: technical services" style="background:linear-gradient(135deg,#c7ccd3,#9096a0)"></div>
  <div class="thumb" role="img" aria-label="Thumbnail photo: partners" style="background:linear-gradient(135deg,#d8c7b0,#a48d72)"></div>
</div>
<svg class="thumb-pointer abs" width="9" height="16" viewBox="0 0 9 16"><polygon points="9,0 0,8 9,16" fill="#4a5a66"/></svg>
<div class="hero abs" role="img" aria-label="Photo: two business people shaking hands"></div>
<div class="hero-tint abs"></div>
<div class="hero-title abs"><span class="chev">›</span>partners</div>
<div class="hero-sub abs">partner with 47VORA award winning team</div>

<section class="audience col-designers abs">
  <svg class="eyebrow-tick" viewBox="0 0 7 14"><polyline points="0,0 6,7 0,14" fill="#fff" stroke="#c6c9cc"/></svg>
  <span class="eyebrow">for graphic designers</span>
  <h2 style="color:var(--magenta)">GET CREATIVE !</h2>
  <div class="visual" role="img" aria-label="Illustration: creative profile with colourful swoosh" style="background:linear-gradient(90deg,#8e2a8c 0%,#c2327c 30%,#f2b6cf 70%,#fff 100%)"></div>
  <p>47Vora is looking for top creative talent to deliver graphic design solutions for some leading global brands Do you have what it takes?</p>
  <span class="learn-more">Learn More</span>
</section>

<section class="audience col-clients abs">
  <svg class="eyebrow-tick" viewBox="0 0 7 14"><polyline points="0,0 6,7 0,14" fill="#fff" stroke="#c6c9cc"/></svg>
  <span class="eyebrow">for clients</span>
  <h2 style="color:var(--orange)">THE 47VORA DIFFERENCE</h2>
  <div class="visual" role="img" aria-label="Illustration: standout figure running ahead of the crowd" style="left:24px;background:linear-gradient(90deg,#d9d9d9,#bdbdbd 60%,#a9a9a9)"></div>
  <p>Smart, Flexible, Thoughtful: find out why leading corporations and government agencies are turning to 47Vora to help manage their most demanding IT services challenges.</p>
  <span class="learn-more" style="left:20px">Learn More</span>
</section>

<section class="audience col-partners abs">
  <svg class="eyebrow-tick" viewBox="0 0 7 14"><polyline points="0,0 6,7 0,14" fill="#fff" stroke="#c6c9cc"/></svg>
  <span class="eyebrow">for partners</span>
  <h2 style="color:var(--sky)">TEAM UP WITH THE BEST</h2>
  <div class="visual" role="img" aria-label="Photo: business handshake in front of office towers" style="left:23px;background:linear-gradient(90deg,#3d3d3d,#9c8a78 50%,#5a6670)"></div>
  <p>When it comes to technology partnerships, our mission it so make you a success.</p>
  <span class="learn-more" style="top:249px">Learn More</span>
</section>

<section class="services abs">
  <h3 style="left:42px;top:36px">Creative Design Services</h3>
  <ul style="left:55px;top:70px">
    <li>Print</li><li>Logo Design</li><li>Website Design</li><li>Illustration</li>
  </ul>
  <h3 style="left:349px;top:36px">Business and Technology solutions</h3>
  <ul style="left:362px;top:70px;width:230px">
    <li>Application Software and Web Development</li>
    <li>Business Process Re-Design (BPR)</li>
    <li>Business/Systems Analysis and Requirement Documentation</li>
    <li>Mentoring and Training</li>
  </ul>
  <ul style="left:612px;top:70px;width:240px">
    <li>Network/Hardware Installation Services</li>
    <li>System Design and Architecture</li>
    <li>Vendor Management</li>
    <li>Docuvault Architecture and Implementation</li>
  </ul>
</section>
<div class="services-divider abs"></div>

<footer class="copyright abs">Copyright 2010, 47Vora, LLC All rights reserved.</footer>

</body>
</html>
```